Mattress sale flyer front and back

FLYER SIZE!! front and back!
4.25" X 5.5"
or
10.7cm X 13.9 cm

This flyer needs to show the prices
twin.....$99
full.......$159
queen...$199
king....$299

the phone number........(786)471-3926
the address ..........24315 sw 142st miami fl 33157
if possible a map would be appreciated

possible brands to include.......Dorvin, Kaplets, brule & nasher, quilmdown

ATTACHED IS OUR OLD FLYER WITH OUTDATED INFORMATION, I WOULD LIKE SOMETHING SIMILAR. JUST ADD A LITTLE PRICE LIST AND A MAP

***FRONT AND BACK PLEASE****

```html
<!DOCTYPE html>
<html lang="en">
<head>
<meta charset="utf-8">
<title>Coral Sleep Outlet – Flyer Front and Back</title>
<link rel="stylesheet" href="https://fonts.googleapis.com/css2?family=Oswald:wght@400;500;600&display=swap">
<style>
  :root {
    --bg: #e9ecee;
    --paper: #ffffff;
    --yellow: #f1e400;
    --blue: #1f4f9e;
    --navy: #0e2348;
    --ink: #15295a;
    --teal: #2aa5b8;
    --map-a: #e6e3dc;
    --map-b: #d9d6ce;
    --mattress-a: #f4f4f4;
    --mattress-b: #dcdcdc;
  }
  * { box-sizing: border-box; margin: 0; padding: 0; }
  html, body { width: 1200px; height: 700px; overflow: hidden; }
  body {
    background: var(--bg);
    font-family: "Oswald", "Arial Narrow", sans-serif;
    color: var(--ink);
    position: relative;
  }
  .flyer {
    position: absolute;
    top: 150px;
    width: 300px;
    height: 400px;
    background: var(--paper);
    overflow: hidden;
    box-shadow: 0 6px 18px rgba(0,0,0,.12);
  }
  .flyer--front { left: 270px; }
  .flyer--back { left: 630px; }
  .band { position: absolute; left: 0; width: 100%; }

  /* brand block */
  .brand {
    display: flex; align-items: center; justify-content: center; gap: 10px;
    height: 100%;
  }
  .brand__mark { width: 18px; height: 18px; background: var(--teal); flex: none; }
  .brand__name {
    font-weight: 400; color: var(--ink); text-transform: uppercase;
    letter-spacing: 2px; line-height: 1;
  }
  .flyer--front .brand__name { font-size: 26px; }
  .flyer--back .brand__name { font-size: 22px; }

  /* front */
  .front-top { top: 10px; height: 138px; background: var(--yellow); }
  .tagline {
    top: 148px; height: 36px; background: var(--blue); color: #fff;
    font-size: 18px; font-weight: 500; text-align: center; line-height: 36px;
  }
  .prices { top: 184px; height: 119px; }
  .prices__photo {
    position: absolute; left: 26px; top: 14px; width: 248px; height: 92px;
    background: linear-gradient(180deg, var(--mattress-a), var(--mattress-b));
    border-radius: 6px;
  }
  .prices__grid {
    position: absolute; inset: 0;
    display: grid; grid-template-columns: auto auto; justify-content: center;
    align-content: center; column-gap: 20px; row-gap: 2px;
    font-size: 23px; font-weight: 600; color: var(--ink); line-height: 1.1;
  }
  .divider { top: 303px; height: 4px; background: var(--blue); }
  .brands {
    top: 310px; height: 50px;
    display: flex; align-items: center; justify-content: center; gap: 14px;
    font-size: 11px; font-weight: 500; color: var(--ink); text-transform: uppercase;
  }
  .brands__item { display: flex; align-items: center; gap: 4px; }
  .brands__badge { width: 12px; height: 12px; background: #c9a24a; border-radius: 50%; }
  .front-foot {
    top: 362px; height: 22px; background: var(--yellow);
    font-size: 9px; font-weight: 500; text-align: center; line-height: 22px;
  }

  /* back */
  .back-top { top: 10px; height: 80px; background: var(--yellow); }
  .headline {
    top: 90px; height: 44px; background: var(--blue); color: #fff;
    font-size: 29px; font-weight: 500; text-align: center; line-height: 44px;
  }
  .map {
    position: absolute; left: 10px; top: 138px; width: 280px; height: 104px;
    border: 3px solid var(--blue);
    background: linear-gradient(135deg, var(--map-a), var(--map-b));
  }
  .contact { top: 252px; height: 78px; background: var(--blue); }
  .contact__tab {
    position: absolute; left: 0; top: 6px; width: 126px; height: 22px;
    background: var(--navy); color: #fff; font-size: 13px; font-weight: 500;
    line-height: 22px; padding-left: 10px;
  }
  .contact__phone-shape { position: absolute; left: 0; top: 30px; }
  .contact__phone {
    position: absolute; left: 10px; top: 38px;
    font-size: 17px; font-weight: 500; color: var(--navy);
  }
  .contact__address {
    position: absolute; right: 10px; top: 14px; width: 128px;
    color: #fff; font-size: 13px; font-weight: 400; line-height: 1.45;
    text-transform: uppercase;
  }
  .social {
    top: 330px; height: 33px; background: var(--navy);
    display: flex; align-items: center; justify-content: center; gap: 10px;
  }
  .social__square { width: 22px; height: 22px; background: var(--blue); }
  .social__links {
    color: #fff; font-size: 5.5px; font-weight: 500; line-height: 1.6;
    text-transform: uppercase;
  }
  .back-foot {
    top: 365px; height: 19px; background: var(--yellow);
    font-size: 9px; font-weight: 500; text-align: center; line-height: 19px;
    color: var(--ink);
  }
</style>
</head>
<body>

<section class="flyer flyer--front" aria-label="Flyer front">
  <div class="band front-top">
    <div class="brand"><span class="brand__mark"></span><span class="brand__name">Coral Sleep Outlet</span></div>
  </div>
  <div class="band tagline">LOWEST PRICES. BEST BRANDS.</div>
  <div class="band prices">
    <div class="prices__photo" role="img" aria-label="Photo of a white quilted mattress"></div>
    <div class="prices__grid">
      <span>TWIN - $99</span><span>FULL - $159</span>
      <span>QUEEN - $199</span><span>KING - $299</span>
    </div>
  </div>
  <div class="band divider"></div>
  <div class="band brands">
    <span class="brands__item">Kaplets</span>
    <span class="brands__item">Dorvin</span>
    <span class="brands__item">Norvale</span>
    <span class="brands__item"><span class="brands__badge"></span>Brule &amp; Nasher</span>
  </div>
  <div class="band front-foot">AND OTHER GREAT BRAND NAMES!</div>
</section>

<section class="flyer flyer--back" aria-label="Flyer back">
  <div class="band back-top">
    <div class="brand"><span class="brand__mark"></span><span class="brand__name">Coral Sleep Outlet</span></div>
  </div>
  <div class="band headline">CONTACT US NOW!</div>
  <div class="map" role="img" aria-label="Street map showing the store location at 24315 SW 142nd St"></div>
  <div class="band contact">
    <div class="contact__tab">CALL US!</div>
    <svg class="contact__phone-shape" width="140" height="40" viewBox="0 0 140 40" aria-hidden="true">
      <polygon points="0,0 118,0 140,40 0,40" fill="var(--yellow)"/>
    </svg>
    <div class="contact__phone">(786)471-3926</div>
    <div class="contact__address">24315 SW 142nd St,<br>Miami, FL 33157, USA</div>
  </div>
  <div class="band social">
    <span class="social__square"></span>
    <div class="social__links">
      <div>https://www.friendline.com/coralsleepoutlet</div>
      <div>https://www.searchly.com/+coralsleepoutlet</div>
      <div>https://www.chirper.com/coralsleepoutlet</div>
    </div>
  </div>
  <div class="band back-foot">HTTP://WWW.CORALSLEEPOUTLET.COM/</div>
</section>

</body>
</html>
```